New Design for our Velostine Gran Reserva Brandy, it is the label design for the bottle label

We need a new bottle label for our Brandy Gran Reserva that we want to bring to the market.

Please have a look at all our current bottles and labels and the feel of our company under www.velostine-example.ch

The bottle that we will be using for the brand is a different one than the one that we already have, the design of the bottle is attached with a document.

I have also attached a briefing in regards to Brandy in general for your information.

### 1. What is Brandy?
Brandy is a distilled spirit made from fermented wine or other fruit wines. It is traditionally aged in oak barrels, which gives it its characteristic color and rich flavor. The aging process in oak is essential for developing the aromas and quality of the brandy.

### 2. What is Brandy Reserva?
A Brandy labeled as "Reserva" has undergone a longer aging process, typically at least 2 to 3 years, in oak barrels. This aging gives the brandy a deeper, more complex flavor profile and a darker color. "Reserva" is often an indication of higher quality.

### 3. Who enjoys drinking Brandy?
Brandy is typically favored by those who appreciate a deep, rich tasting experience. This often includes older consumers who value the time-aged complexity of the spirit. However, Brandy is also gaining popularity among younger people, especially through cocktails and modern serving styles.

### 4. Why is Brandy trending?
Brandy is experiencing a resurgence as consumers increasingly value quality and artisanal production methods. Its versatility in cocktails and association with traditional, luxurious experiences have also contributed to its renewed popularity.

### 5. What colors would be associated with Brandy?
The typical colors associated with Brandy are warm gold, amber, and deep golden-brown tones. These colors reflect the aging process in oak barrels and the richness of the flavors. Other associated colors might include dark brown and mahogany.

### 6. What is important to customers when buying Brandy?
Customers care about the origin of the Brandy, the aging time, the quality of the ingredients, the production method, and the brand. They also pay attention to the prestige of the product and the authenticity of the production.

### 7. What is not important to customers when buying Brandy?
For many customers, the price and packaging (unless it’s especially exclusive) may be less important than the quality and taste of the Brandy. The distillery name might be less significant if it isn’t tied to a particular reputation.

### 8. What do customers know about Swiss Brandy?
Swiss Brandy is still relatively unknown in many markets, but customers who are familiar with it appreciate the precision and quality of Swiss production. Swiss Brandy is assumed to be made with care and under strict quality standards.

### 9. What is Brandy Gran Reserva?
**Brandy Gran Reserva** is an even higher quality and longer-aged version of Brandy. Generally, a Gran Reserva is aged for at least 5 to 10 years or more in oak barrels. This extended aging process gives the Brandy an especially deep, complex flavor profile and often a darker, richer color. Gran Reserva is often regarded as the top-tier product within a Brandy range and appeals to discerning consumers who value quality, refinement, and a luxurious tasting experience.

The label “Gran Reserva” thus indicates the highest quality level for Brandies, similar to other spirits (like wine or whisky), where the aging time is a critical factor.

### 10. What emotions are associated with Brandy?
Brandy is often associated with luxury, relaxation, and comfort. It evokes feelings of tradition, elegance, and sophistication. Drinking Brandy is frequently seen as a moment of reflection and enjoyment.

### 11. How should Brandy be marketed?
Brandy should be marketed with a focus on its artisanal production, quality, and tradition. A narrative around the product, its aging, and origin can help create an emotional connection with the customer. The marketing should also emphasize the versatility of Brandy, whether consumed neat or in cocktails.

### 12. Sales test and label design for Velostine Brandy
For a sales test, I would suggest a tasting in an upscale setting, perhaps paired with a storytelling presentation highlighting the history of the 6-year aged Brandy and its aging in oak barrels.

**Label design**:
The label should reflect the exclusivity of the product, with an elegant, minimalist design. Colors like deep gold, mahogany, and a hint of deep blue could be used to emphasize the aging and quality of the Brandy. The label should include information about the aging time, the use of oak barrels, and a brief story about the Brandy’s production. A seal or embossing highlighting the craftsmanship would also be fitting.

Target Market(s)

Customers that like Brandy

Requirements
Must have
• the Alcohol % must be included on the label as well as our address.

```html
<!DOCTYPE html>
<html lang="en">
<head>
<meta charset="utf-8">
<title>Velostine Brandy Gran Reserva – Bottle Label</title>
<link rel="stylesheet" href="https://fonts.googleapis.com/css2?family=Cinzel:wght@400;700&family=Roboto+Slab:wght@700&display=swap">
<style>
  :root {
    --page: #ffffff;
    --wine-light: #8e1d38;
    --wine-dark: #5a1a2b;
    --gold-light: #f0c96a;
    --gold: #c8962e;
    --gold-dark: #9a6a1c;
    --ink: #1a1a1a;
    --white: #ffffff;
  }
  html, body {
    margin: 0;
    width: 1200px;
    height: 960px;
    overflow: hidden;
    background: var(--page);
  }
  .canvas {
    position: relative;
    width: 1200px;
    height: 960px;
  }
  .label-frame {
    position: absolute;
    left: 390px;
    top: 100px;
    width: 420px;
    height: 740px;
    background: linear-gradient(135deg, var(--gold-light), var(--gold) 45%, var(--gold-dark) 75%, var(--gold-light));
    clip-path: polygon(0 0, 100% 0, 95.5% 100%, 4.5% 100%);
  }
  .label {
    position: absolute;
    inset: 12px 14px;
    background: linear-gradient(90deg, var(--wine-dark), var(--wine-light) 45%, var(--wine-dark));
    clip-path: polygon(0 0, 100% 0, 95.5% 100%, 4.5% 100%);
    text-align: center;
    color: var(--gold);
    font-family: "Cinzel", serif;
  }
  .crest {
    position: absolute;
    left: 50%;
    top: 34px;
    width: 44px;
    height: 56px;
    margin-left: -22px;
    background: linear-gradient(180deg, var(--gold-light), var(--gold-dark));
    border-radius: 6px;
  }
  .brand-name {
    position: absolute;
    top: 108px;
    width: 100%;
    font-family: "Cinzel", serif;
    font-weight: 700;
    font-size: 40px;
    color: var(--white);
    letter-spacing: 1px;
  }
  .brand-sub {
    position: absolute;
    top: 160px;
    width: 100%;
    font-family: "Roboto Slab", serif;
    font-weight: 700;
    font-size: 15px;
    line-height: 18px;
    color: var(--white);
    letter-spacing: 1px;
  }
  .rule {
    position: absolute;
    left: 60px;
    right: 60px;
    height: 1px;
    background: linear-gradient(90deg, transparent, var(--gold-light), transparent);
  }
  .rule-top { top: 218px; }
  .rule-bottom { top: 327px; }
  .product {
    position: absolute;
    top: 226px;
    width: 100%;
    font-size: 58px;
    line-height: 66px;
    background: linear-gradient(180deg, var(--gold-light), var(--gold-dark));
    -webkit-background-clip: text;
    background-clip: text;
    color: transparent;
  }
  .grade {
    position: absolute;
    top: 294px;
    width: 100%;
    font-size: 17px;
    letter-spacing: 9px;
    color: var(--gold-light);
  }
  .established {
    position: absolute;
    top: 346px;
    width: 100%;
    font-size: 11px;
    letter-spacing: 5px;
    color: var(--gold-light);
  }
  .emblem {
    position: absolute;
    left: 50%;
    top: 392px;
    width: 150px;
    height: 150px;
    margin-left: -75px;
    background: linear-gradient(180deg, rgba(240,201,106,0.35), rgba(154,106,28,0.25));
    border-radius: 4px;
  }
  .seal-mark {
    position: absolute;
    left: 50%;
    top: 563px;
    width: 10px;
    height: 10px;
    margin-left: -5px;
    background: var(--gold);
    border-radius: 50%;
  }
  .story-panel {
    position: absolute;
    left: 66px;
    right: 66px;
    top: 582px;
    height: 86px;
  }
  .story-panel svg { position: absolute; inset: 0; }
  .story-text {
    position: absolute;
    left: 60px;
    right: 60px;
    top: 8px;
    font-family: "Cinzel", serif;
    font-size: 9px;
    line-height: 11px;
    color: var(--white);
  }
  .abv {
    position: absolute;
    left: 0;
    right: 0;
    top: 68px;
    font-size: 9px;
    letter-spacing: 4px;
    color: var(--gold-light);
  }
  .foot-mark {
    position: absolute;
    left: 50%;
    bottom: 8px;
    width: 14px;
    height: 12px;
    margin-left: -7px;
    background: var(--gold);
    border-radius: 3px;
  }
  .corner-brand {
    position: absolute;
    left: 84px;
    top: 800px;
    width: 120px;
    text-align: center;
    color: var(--ink);
  }
  .corner-brand .name {
    font-family: "Cinzel", serif;
    font-weight: 700;
    font-size: 26px;
    line-height: 30px;
  }
  .corner-brand .sub {
    font-family: "Roboto Slab", serif;
    font-weight: 700;
    font-size: 10px;
    line-height: 11px;
    letter-spacing: 0.5px;
  }
</style>
</head>
<body>
<main class="canvas">
  <section class="label-frame">
    <div class="label">
      <div class="crest" role="img" aria-label="Gold fleur ornament with small heart"></div>
      <div class="brand-name">Velostine</div>
      <div class="brand-sub">SWISS<br>DISTILLERY</div>
      <div class="rule rule-top"></div>
      <div class="product">BRANDY</div>
      <div class="grade">GRAN RESERVA</div>
      <div class="rule rule-bottom"></div>
      <div class="established">EST. 2024</div>
      <div class="emblem" role="img" aria-label="Gold line illustration of a distillery house framed by three wheat ears"></div>
      <div class="seal-mark"></div>
      <div class="story-panel">
        <svg width="100%" height="86" viewBox="0 0 256 86" preserveAspectRatio="none" aria-hidden="true">
          <rect x="0.5" y="0.5" width="255" height="46" fill="none" stroke="#c8962e" stroke-width="1"/>
          <circle cx="20" cy="23" r="11" fill="none" stroke="#c8962e" stroke-width="1"/>
          <circle cx="236" cy="23" r="11" fill="none" stroke="#c8962e" stroke-width="1"/>
          <rect x="0.5" y="56.5" width="255" height="29" fill="none" stroke="#c8962e" stroke-width="1"/>
        </svg>
        <div class="story-text">The Story Of Our Six Year Aged Brandy Rested In Oak Barrels</div>
        <div class="abv">ALCOHOL 35%</div>
      </div>
      <div class="foot-mark"></div>
    </div>
  </section>
  <div class="corner-brand">
    <div class="name">Velostine</div>
    <div class="sub">SWISS<br>DISTILLERY</div>
  </div>
</main>
</body>
</html>
```